Quillbrookes websites redesign

Www.quill-brookes.com needs to be redesigned along with updations. The incremental material will be provided for the updations. We are looking for complete redesign of the pages with the new content. The complete write up will be provided soon

Target Market(s)

Global

Coding

Coded - Design and coding required

Number of Pages Required

5+ page

Requirements
Must have
• A clean and slick design for the Consulting.
Should not have
• Too many pictures which reduces the speed of the site

```html
<!DOCTYPE html>
<html lang="en">
<head>
<meta charset="utf-8">
<title>Quillbrookes Consultancy</title>
<link href="https://fonts.googleapis.com/css2?family=Roboto:wght@400;500;700&family=Raleway:wght@400;500;600&display=swap" rel="stylesheet">
<style>
:root{
  --navy:#2b3a57;
  --navy-dark:#1f2b43;
  --navy-deep:#223049;
  --ink:#2a2f3a;
  --muted:#555b66;
  --maroon:#7a2a2a;
  --olive:#9b901f;
  --paper:#ffffff;
  --mist:#f1f2f3;
  --line:#d9dbe0;
}
*{box-sizing:border-box;margin:0;padding:0}
html,body{width:1200px;height:2184px;overflow:hidden}
body{position:relative;background:var(--paper);font-family:'Roboto',sans-serif;color:var(--ink)}
.abs{position:absolute}

/* header */
.site-header{position:absolute;left:0;top:0;width:1200px;height:84px;background:#fff;border-top:3px solid var(--navy-dark)}
.brand{position:absolute;left:99px;top:25px;display:flex;align-items:center;gap:12px}
.brand-dot{width:34px;height:34px;border-radius:50%;background:var(--navy)}
.brand-name{font-family:'Roboto',sans-serif;font-size:31px;font-weight:400;color:var(--navy-dark)}
.main-nav a{position:absolute;top:38px;font-size:13.5px;color:#333;text-decoration:none;transform:translateX(-50%)}
.main-nav a.is-active{color:var(--maroon)}

/* hero */
.hero{position:absolute;left:0;top:84px;width:1200px;height:487px;
  background:linear-gradient(100deg,#6f6a63 0%,#b9b1a4 25%,#d8d1c3 45%,#9a958d 70%,#c8c4bb 100%)}
.hero-caption{position:absolute;left:584px;top:113px;width:515px;height:247px;background:rgba(80,80,80,.72);padding:28px 38px;color:#fff}
.hero-title{font-family:'Roboto',sans-serif;font-weight:700;font-size:48px;letter-spacing:.5px;line-height:1}
.hero-text{font-size:23px;line-height:38px;margin-top:18px}
.hero-more{font-size:21px;margin-top:18px;display:block}
.hero-arrow{position:absolute;top:230px}

/* about */
.about{position:absolute;left:0;top:571px;width:1200px;height:258px;background:linear-gradient(180deg,#3c4a66,#202c44);box-shadow:0 14px 18px -10px rgba(0,0,0,.35)}
.about-visual{position:absolute;right:0;top:0;width:565px;height:258px;background:linear-gradient(120deg,#2a3752 0%,#1d6fb8 55%,#8cc8ff 75%,#2c2c2c 100%)}
.about h2{position:absolute;left:99px;top:28px;font-family:'Roboto',sans-serif;font-weight:400;font-size:22px;color:#fff}
.about p{position:absolute;left:99px;top:72px;width:560px;font-size:11.3px;line-height:24px;color:#e6e9f0}
.about .read-more{position:absolute;left:99px;top:211px;font-size:13px;color:#fff}

/* trade */
.trade-title{position:absolute;left:0;width:1200px;text-align:center;font-family:'Raleway',sans-serif;color:var(--navy-dark)}
.trade-circle{position:absolute;width:112px;height:112px;border-radius:50%;border:7px solid #36425a;background:radial-gradient(circle at 50% 35%,#fff,#e3e6ea);display:flex;align-items:center;justify-content:center;font-family:'Raleway',sans-serif;font-weight:600;color:#263248;box-shadow:0 10px 10px -6px rgba(0,0,0,.25)}
.trade-arrow{position:absolute;top:1060px}

/* case studies */
.cases{position:absolute;left:0;top:1198px;width:1200px;height:437px;background:var(--mist)}
.section-title{position:absolute;left:0;width:1200px;text-align:center;font-family:'Raleway',sans-serif;font-weight:500;font-size:20px;color:var(--navy-dark)}
.case-card{position:absolute;top:112px;width:314px}
.case-photo{width:314px;height:182px;border:4px solid #fff;box-shadow:0 0 0 1px var(--line)}
.case-name{margin-top:24px;font-size:15px;line-height:26px;color:#444;padding-left:0}
.case-link{position:absolute;top:272px;font-size:11.5px;color:var(--maroon)}

/* newsletter */
.email-field{position:absolute;left:285px;top:1765px;width:376px;height:43px;border:1px solid var(--line);background:#fff;padding:0 16px;font-size:15px;color:#aaa;display:flex;align-items:center}
.subscribe-btn{position:absolute;left:695px;top:1765px;width:173px;height:43px;background:var(--olive);color:#fff;font-size:15px;display:flex;align-items:center;justify-content:center}

/* footer */
.site-footer{position:absolute;left:0;top:1868px;width:1200px;height:243px;background:var(--navy)}
.footer-col{position:absolute;top:45px;color:#fff}
.footer-col h3{font-family:'Roboto',sans-serif;font-weight:500;font-size:18px;margin-bottom:22px}
.footer-col li{list-style:none;font-size:13.5px;line-height:31px;color:#e3e6ee}
.footer-col.links li{font-size:13px;line-height:29px}
.footer-col.address li{font-size:15px;line-height:38px}
.footer-email{position:absolute;left:753px;top:99px;width:348px;height:43px;display:flex}
.footer-email span{flex:1;background:#fff;font-size:11px;color:#999;padding:0 14px;display:flex;align-items:center}
.footer-email i{width:47px;background:var(--navy-dark);display:flex;align-items:center;justify-content:center}
.social{position:absolute;left:805px;top:172px;display:flex;gap:28px}
.social span{width:18px;height:18px;border-radius:50%;background:#fff;display:block}
.copyright-bar{position:absolute;left:0;top:2111px;width:1200px;height:73px;background:var(--navy-dark);color:#e3e6ee;font-size:14px;display:flex;align-items:center;justify-content:center}
</style>
</head>
<body>

<header class="site-header">
  <div class="brand"><span class="brand-dot"></span><span class="brand-name">Quillbrookes</span></div>
  <nav class="main-nav">
    <a class="is-active" style="left:491px">Home</a>
    <a style="left:592px">Founder</a>
    <a style="left:713px">Consultancy</a>
    <a style="left:830px">System</a>
    <a style="left:948px">Case Studies</a>
    <a style="left:1068px">Contact</a>
  </nav>
</header>

<section class="hero" role="img" aria-label="Photo of a hand writing with a pen over financial charts and graphs">
  <svg class="hero-arrow" style="left:46px" width="18" height="28" viewBox="0 0 18 28"><path d="M14 3 4 14l10 11" fill="none" stroke="#fff" stroke-width="3"/></svg>
  <svg class="hero-arrow" style="left:1137px" width="18" height="28" viewBox="0 0 18 28"><path d="M4 3l10 11L4 25" fill="none" stroke="#fff" stroke-width="3"/></svg>
  <div class="hero-caption">
    <h1 class="hero-title">QUILLBROOKES</h1>
    <p class="hero-text">Provide consultancy services to Emerging country banks, Corporates and SMEs.</p>
    <span class="hero-more">[ More Info ]</span>
  </div>
</section>

<section class="about">
  <div class="about-visual" role="img" aria-label="Businessman drawing a glowing blue rising bar chart"></div>
  <h2>About Us</h2>
  <p>Quillbrookes Consultancy Limited capitalizes on synergies arising from trade and investment linkages between countries and knowledge of traditional and non-traditional pools of liquidity to provide consultancy services to Emerging country banks, Corporates and SMEs. The Consultancy provides bank neutral views to Corporates and SMEs in Asian emerging markets and helps in improving financial structure and efficient use of funds</p>
  <span class="read-more">[ Read More ]</span>
</section>

<h2 class="trade-title" style="top:892px;font-size:19px;font-weight:500">WORLD MERCHANDISING TRADE 2012 ( USD BILLION)</h2>
<p class="trade-title" style="top:934px;font-size:20px;font-weight:500;color:#333">Global Trade Council</p>

<div class="trade-circle" style="left:203px;top:1011px;font-size:22px">0 - 250</div>
<div class="trade-circle" style="left:426px;top:1011px;font-size:18px">250-500</div>
<div class="trade-circle" style="left:652px;top:1011px;font-size:16px">500-1000</div>
<div class="trade-circle" style="left:883px;top:1011px;font-size:22px">&gt; 1000</div>
<svg class="trade-arrow" style="left:352px" width="36" height="20" viewBox="0 0 36 20"><path d="M2 6q16 10 28 6M24 6l7 6-8 5" fill="none" stroke="#c9ccd2" stroke-width="4"/></svg>
<svg class="trade-arrow" style="left:578px" width="36" height="20" viewBox="0 0 36 20"><path d="M2 16q14-12 28-8M24 2l7 6-8 5" fill="none" stroke="#c9ccd2" stroke-width="4"/></svg>
<svg class="trade-arrow" style="left:808px" width="36" height="20" viewBox="0 0 36 20"><path d="M2 6q16 10 28 6M24 6l7 6-8 5" fill="none" stroke="#c9ccd2" stroke-width="4"/></svg>

<section class="cases">
  <h2 class="section-title" style="top:48px">OUR CASE STUDIES</h2>
  <article class="case-card" style="left:99px">
    <div class="case-photo" role="img" aria-label="Blue stock market ticker screen with figures" style="background:linear-gradient(135deg,#0d2f7a,#3b7fd0 60%,#9fc6f0)"></div>
    <p class="case-name">Export Credit Agency backed long term Project financing</p>
    <span class="case-link" style="left:4px">[ Case Studies ]</span>
  </article>
  <article class="case-card" style="left:444px">
    <div class="case-photo" role="img" aria-label="Hands using a tablet beside financial papers" style="background:linear-gradient(135deg,#e8eef3,#9bb6cc 55%,#d8e2ea)"></div>
    <p class="case-name">Introducing Regional/Local banks for International Subsidiary Banking</p>
    <span class="case-link" style="left:4px">[ Case Studies ]</span>
  </article>
  <article class="case-card" style="left:788px">
    <div class="case-photo" role="img" aria-label="Silhouettes of business people in a meeting room" style="background:linear-gradient(180deg,#e9eef2,#b7c2cc 60%,#1c2430)"></div>
    <p class="case-name" style="padding-top:4px">Structured Financing</p>
    <span class="case-link" style="left:6px">[ Case Studies ]</span>
  </article>
</section>

<h2 class="section-title" style="top:1694px;color:#111">NEWSLETTER SIGNUP</h2>
<div class="email-field">Email</div>
<div class="subscribe-btn">Subscribe</div>

<footer class="site-footer">
  <div class="footer-col" style="left:99px">
    <h3>New Business</h3>
    <ul><li>info @ quillbrookes.com</li><li>quillbrookes.domain.com</li><li>120.448.19 / 031.572.806</li></ul>
  </div>
  <div class="footer-col address" style="left:333px">
    <h3>Our Adderss</h3>
    <ul><li>1234 Alder Lane</li><li>Fairhaven, PA 12457</li></ul>
  </div>
  <div class="footer-col links" style="left:550px">
    <h3>Links</h3>
    <ul><li>Eum choro dolorem</li><li>Pri nibh decore</li><li>Eum choro dolorem</li><li>Pri nibh decore</li></ul>
  </div>
  <div class="footer-col" style="left:753px">
    <h3>Newstetter Singup</h3>
  </div>
  <div class="footer-email"><span>Your Email Here . .</span><i><svg width="16" height="14" viewBox="0 0 16 14"><path d="M1 5h14v8H1zM1 5l7 5 7-5M4 5V1h8v4" fill="none" stroke="#fff" stroke-width="1.4"/></svg></i></div>
  <div class="social"><span></span><span></span><span></span><span></span><span></span><span></span><span></span></div>
</footer>
<div class="copyright-bar">All Rights Reserved . Copyrights2016@quillbrookes.com</div>

</body>
</html>
```